Fenwick Grading LTD - website for irrigation & Landscape Lighting & Buried service wire

Looking for a website to help promote my business with Irrigation (installation, service, etc) and buried service wire/drainage solutions.

Commercial/Residential

Landscape lighting.

I’ll get photos in the trucks and trailers to upload as well maybe the machine as well.

Target Market(s)

Homeowners who want green grass and beautiful gardens. Beautiful landscape lighting

Industry/Entity Type

Irrigation systems and landscape lighting and buried service wire to homes and offering Drainage soltions.

Coding

Coded - Design and coding required

Number of Pages Required

4 page

Colors
F0912C
F2A743
F7CA91
FBE8D2
FDF5EE

Requirements
Must have
• was hoping to link up my email on fenwickgrading@mailbox-example.net with the website if possible.
Nice to have
• Page for Irrigation, page for landscape lighting, page buried service wire & drainage soltions.

```html
<!DOCTYPE html>
<html lang="en">
<head>
<meta charset="utf-8">
<title>Fenwick Grading LTD</title>
<link href="https://fonts.googleapis.com/css2?family=Montserrat:wght@400;500;600&family=Oswald:wght@500&display=swap" rel="stylesheet">
<style>
:root{
  --orange:#F0912C;
  --orange-2:#F2A743;
  --peach:#F7CA91;
  --cream:#FBE8D2;
  --ivory:#FDF5EE;
  --ink:#111111;
  --muted:#555555;
  --white:#ffffff;
}
*{margin:0;padding:0;box-sizing:border-box}
html,body{width:1200px;height:2975px;overflow:hidden}
body{position:relative;background:var(--white);font-family:'Montserrat',sans-serif;color:var(--ink)}
.abs{position:absolute}
a{color:inherit;text-decoration:none}

/* hero */
.hero{left:0;top:0;width:1200px;height:625px;background:linear-gradient(160deg,#2c3a1f 0%,#4a5e2c 35%,#3d4a2a 60%,#55603a 100%)}
.hero-shade{left:0;top:0;width:1200px;height:625px;background:linear-gradient(90deg,rgba(0,0,0,.45),rgba(0,0,0,.15))}
.hero-edge{left:0;top:530px;width:1200px;height:100px}
.brand{left:141px;top:34px;display:flex;align-items:center;gap:10px;color:var(--white);font-weight:600;font-size:17px;line-height:1.15;letter-spacing:.5px}
.brand-mark{width:14px;height:14px;background:var(--orange)}
.nav{right:142px;top:25px;display:flex;align-items:center;gap:29px;font-size:12.5px;font-weight:500;color:var(--white)}
.btn{display:inline-block;background:var(--orange);color:var(--white);font-size:12.5px;font-weight:500}
.nav .btn{padding:13px 20px}
.hero-title{left:141px;top:178px;width:470px;font-family:'Oswald',sans-serif;font-weight:500;font-size:36px;line-height:48px;color:var(--white)}
.hero-text{left:141px;top:335px;width:455px;font-size:12.5px;line-height:22.5px;color:var(--white)}
.hero-btn{left:141px;top:416px;padding:13px 19px}

/* services */
.blob{width:390px;height:390px}
.svc-title{font-size:25px;font-weight:500}
.svc-title span,.accent{color:var(--orange)}
.svc-lead{border-left:1px solid var(--orange);padding-left:12px;font-size:12.5px;line-height:22.5px;font-weight:500;width:410px}
.svc-body{font-size:12.5px;line-height:22.5px;color:var(--muted);width:420px}
.pill{background:var(--orange);color:var(--white);font-size:12px;font-weight:600;letter-spacing:1px;border-radius:20px;padding:10px 19px}

/* testimonials */
.t-title{left:0;width:1200px;top:2125px;text-align:center;font-size:25px;font-weight:500}
.t-sub{left:0;width:1200px;top:2176px;text-align:center;font-size:13px;font-weight:500}
.t-quote{left:141px;top:2307px;width:480px;font-size:12.5px;line-height:22.5px}
.t-name{left:141px;top:2436px;font-size:15px;font-weight:500;color:var(--orange)}
.t-arrows{left:141px;top:2510px}

/* footer */
.footer{left:0;top:2662px;width:1200px;height:313px;background:linear-gradient(180deg,#22271f,#2a2f22 60%,#1c1f18)}
.f-brand{left:141px;top:2765px;color:var(--white);font-weight:600;font-size:26px;line-height:1.2;display:flex;gap:12px;align-items:center}
.f-brand .brand-mark{width:20px;height:20px}
.f-col h4{color:var(--orange);font-size:15.5px;font-weight:500;margin-bottom:12px}
.f-col li{list-style:none;color:var(--white);font-size:13px;line-height:27.5px}
.f-contact li{display:flex;gap:12px;align-items:flex-start;line-height:20px;margin-bottom:12px}
.f-rule{left:141px;top:2919px;width:917px;height:1px;background:rgba(255,255,255,.25)}
.copy{left:141px;top:2938px;font-size:13px;color:var(--white)}
.social{right:142px;top:2935px;display:flex;gap:10px}
.social span{width:25px;height:25px;border-radius:50%;background:var(--orange)}
</style>
</head>
<body>

<header>
  <div class="abs hero" role="img" aria-label="Evening garden lawn with lit pathway lights and shrubs"></div>
  <div class="abs hero-shade"></div>
  <svg class="abs hero-edge" viewBox="0 0 1200 100" preserveAspectRatio="none">
    <polygon points="0,12 600,92 1200,12 1200,100 0,100" fill="#ffffff"/>
    <polyline points="0,12 600,92 1200,12" fill="none" stroke="var(--orange)" stroke-width="2"/>
  </svg>
  <div class="abs brand"><span class="brand-mark"></span><span>Fenwick Grading<br>LTD</span></div>
  <nav class="abs nav">
    <a href="#">Home</a><a href="#">Irrigation</a><a href="#">Landscape Lighting</a><a href="#">Service Wire &amp; Drainage</a><a class="btn" href="#">Contact Us</a>
  </nav>
  <h1 class="abs hero-title">Transform Your Outdoor Space With Our Expert Irrigation And Lighting Solutions</h1>
  <p class="abs hero-text">Get the perfect blend of form and function with our state-of-the-art irrigation systems and landscape lighting. Trust our experienced team to deliver buried service wire and drainage for your home</p>
  <a class="abs btn hero-btn" href="#">Contact Us</a>
</header>

<svg width="0" height="0" style="position:absolute">
  <defs>
    <path id="blob-shape" d="M170 12 C240 -2 320 80 340 175 C358 265 280 300 180 340 C90 376 18 372 8 318 C-2 250 70 40 170 12 Z"/>
    <path id="blob-ring" d="M178 6 C252 -6 342 82 356 178 C370 272 290 312 190 350 C96 386 30 384 20 334"/>
    <linearGradient id="g-sky" x1="0" y1="0" x2="0" y2="1"><stop offset="0" stop-color="#a8b8cc"/><stop offset="1" stop-color="#6c7a6e"/></linearGradient>
    <linearGradient id="g-garden" x1="0" y1="0" x2="0" y2="1"><stop offset="0" stop-color="#3c4a2e"/><stop offset="1" stop-color="#5f7b32"/></linearGradient>
    <linearGradient id="g-trench" x1="0" y1="0" x2="1" y2="1"><stop offset="0" stop-color="#c9b79c"/><stop offset="1" stop-color="#5a3f28"/></linearGradient>
    <linearGradient id="g-person" x1="0" y1="0" x2="0" y2="1"><stop offset="0" stop-color="#b9c3c9"/><stop offset="1" stop-color="#2b2f36"/></linearGradient>
  </defs>
</svg>

<section>
  <svg class="abs blob" style="left:150px;top:700px" viewBox="0 0 380 380" role="img" aria-label="Irrigation sprinkler spraying water over a field">
    <use href="#blob-shape" fill="url(#g-sky)"/><use href="#blob-ring" fill="none" stroke="var(--orange)" stroke-width="1.5"/>
  </svg>
  <h2 class="abs svc-title" style="left:639px;top:743px">Irrigation <span>Systems</span></h2>
  <p class="abs svc-lead" style="left:639px;top:798px">Efficient and Effective Watering Solutions for Your Lawn and Garden</p>
  <p class="abs svc-body" style="left:639px;top:858px">Our irrigation systems are designed to provide your lawn and garden with the right amount of water, without wasting a single drop. With our expert installation and service, you can rest assured that your plants will receive the nourishment they need to thrive.</p>
  <a class="abs pill" style="left:639px;top:996px" href="#">LEARN MORE</a>

  <svg class="abs blob" style="left:665px;top:1177px" viewBox="0 0 380 380" role="img" aria-label="Garden lawn at dusk with lit bollard lights">
    <use href="#blob-shape" fill="url(#g-garden)"/><use href="#blob-ring" fill="none" stroke="var(--orange)" stroke-width="1.5"/>
  </svg>
  <h2 class="abs svc-title" style="left:141px;top:1221px">Landscape <span>Lighting</span></h2>
  <p class="abs svc-lead" style="left:141px;top:1275px">Enhance Your Outdoor Space with Beautiful and Functional Lighting Solutions</p>
  <p class="abs svc-body" style="left:141px;top:1335px">Our landscape lighting solutions are designed to enhance the beauty and functionality of your outdoor space. From subtle pathway lighting to dramatic spotlights, we'll work with you to create a lighting plan that meets your needs and complements your landscape.</p>
  <a class="abs pill" style="left:141px;top:1473px" href="#">LEARN MORE</a>

  <svg class="abs blob" style="left:150px;top:1655px" viewBox="0 0 380 380" role="img" aria-label="Crew laying buried service wire and drain pipe in a trench">
    <use href="#blob-shape" fill="url(#g-trench)"/><use href="#blob-ring" fill="none" stroke="var(--orange)" stroke-width="1.5"/>
  </svg>
  <h2 class="abs svc-title" style="left:639px;top:1721px">Service Wire <span>&amp; Drainage</span></h2>
  <p class="abs svc-lead" style="left:639px;top:1775px">Buried Service Wire and Drainage Solutions for Your Property</p>
  <p class="abs svc-body" style="left:639px;top:1813px">Our crew trenches and buries service wire to your home with precision and care, and installs drainage that keeps water away from lawns and foundations. Residential or commercial, we leave your yard clean and ready.</p>
  <a class="abs pill" style="left:639px;top:1928px" href="#">LEARN MORE</a>
</section>

<section>
  <h2 class="abs t-title">What Our <span class="accent">Customers</span> Say</h2>
  <p class="abs t-sub">Hear from Our Satisfied Clients</p>
  <p class="abs t-quote">They maintain around 52 acres for us including several thousand sq ft or beds. Always answer thr phone and very prompt if we ever have an issue. Great guys all the way around! It is a long established fact that a reader will be distracted by the readable content of a page when looking at its layout.</p>
  <p class="abs t-name">Marcus Delaney</p>
  <svg class="abs t-arrows" width="130" height="20" viewBox="0 0 130 20">
    <path d="M36 10H2M10 3L2 10l8 7" fill="none" stroke="#111" stroke-width="1.5"/>
    <path d="M92 10h34M118 3l8 7-8 7" fill="none" stroke="#111" stroke-width="1.5"/>
  </svg>
  <svg class="abs" style="left:705px;top:2232px" width="245" height="350" viewBox="0 0 245 350" role="img" aria-label="Portrait of the featured customer">
    <path d="M118 4 C185 4 232 50 232 130 L232 230 C232 300 190 338 120 338 C50 338 8 300 8 230 L8 130 C8 50 52 4 118 4Z" fill="url(#g-person)"/>
    <path d="M130 6 C198 10 240 60 240 140 L240 236 C240 306 196 344 126 344" fill="none" stroke="var(--orange)" stroke-width="1.5"/>
  </svg>
  <svg class="abs" style="left:945px;top:2185px" width="112" height="112" role="img" aria-label="Portrait of a customer"><circle cx="56" cy="56" r="55" fill="#b2656a"/></svg>
  <svg class="abs" style="left:591px;top:2455px" width="82" height="82" role="img" aria-label="Portrait of a customer"><circle cx="41" cy="41" r="40" fill="#3f6b6c"/></svg>
  <svg class="abs" style="left:966px;top:2465px" width="72" height="72" role="img" aria-label="Portrait of a customer"><circle cx="36" cy="36" r="35" fill="#5d6a6a"/></svg>
</section>

<footer>
  <div class="abs footer" role="img" aria-label="Dim evening garden backdrop"></div>
  <div class="abs f-brand"><span class="brand-mark"></span><span>Fenwick Grading<br>LTD</span></div>
  <div class="abs f-col" style="left:459px;top:2718px">
    <h4>Quick Links</h4>
    <ul><li>Home</li><li>Irrigation</li><li>Landscape Lighting</li><li>Service Wire &amp; Drainage</li></ul>
  </div>
  <div class="abs f-col" style="left:670px;top:2718px">
    <h4>Useful Links</h4>
    <ul><li>Contact</li><li>Privacy Policy</li><li>Terms of Service</li></ul>
  </div>
  <div class="abs f-col f-contact" style="left:839px;top:2718px">
    <h4>Contact Info</h4>
    <ul>
      <li><svg width="16" height="18" viewBox="0 0 16 18"><path d="M8 1a5.5 5.5 0 0 0-5.5 5.5C2.5 11 8 16 8 16s5.5-5 5.5-9.5A5.5 5.5 0 0 0 8 1z" fill="none" stroke="var(--orange)" stroke-width="1.6"/><circle cx="8" cy="6.5" r="2" fill="var(--orange)"/></svg><span>Address Line 1, Address<br>Line 2, Address Line 3.</span></li>
      <li><svg width="16" height="14" viewBox="0 0 16 14"><rect x="1" y="2" width="14" height="10" fill="var(--orange)"/><path d="M1 2l7 6 7-6" fill="none" stroke="#2a2f22" stroke-width="1.3"/></svg><span style="font-size:12px">fenwickgrading@mailbox-example.net</span></li>
      <li><svg width="16" height="16" viewBox="0 0 16 16"><path d="M3 1l3 3-1.5 2c1 2 3 4 5 5L11.5 9.5l3 3-2 2.5C7 14 2 9 1 3z" fill="var(--orange)"/></svg><span>123-456-7890</span></li>
    </ul>
  </div>
  <div class="abs f-rule"></div>
  <p class="abs copy">© 2024 Fenwick Grading. All rights reserved.</p>
  <div class="abs social"><span></span><span></span><span></span><span></span></div>
</footer>

</body>
</html>
```